Verlindo Magician

I want the business card for my business to give to people who watch that later I will be employed to show magic here is my website http://www.verlindoillusions.example/I want the interesting design , i am very opened for formal and informal, I watch a lot of design so don't stick to the common shape and form but i hope it can also be produced the thing to write on will be the same as in picture that i will upload , i also will upload the logo for you that so can be easy to useDenis CostilleMagicianMAGICIAN VERLINDO 17 rue des Tilleuls - 25000 BESANÇON contact@verlindoillusions.example tel. 0381 946 157 tel. 0674 219 503

```html
<!DOCTYPE html>
<html lang="en">
<head>
<meta charset="utf-8">
<title>Verlindo Magician – Business Card</title>
<link href="https://fonts.googleapis.com/css2?family=Jost:wght@300;400&display=swap" rel="stylesheet">
<style>
  :root {
    --backdrop: #232222;
    --card-white: #ffffff;
    --card-red: #ec2426;
    --ink: #111111;
    --ink-soft: #4a4a4a;
    --accent-red: #e3262a;
    --silhouette: #0d0d0d;
  }
  html, body {
    margin: 0;
    padding: 0;
    overflow: hidden;
  }
  body {
    width: 1125px;
    height: 1200px;
    background: var(--backdrop);
    position: relative;
    font-family: "Jost", sans-serif;
  }
  .card {
    position: absolute;
    left: 171px;
    width: 826px;
    height: 471px;
    box-shadow: 0 3px 6px rgba(0,0,0,0.55);
  }
  .card--front { top: 106px; background: var(--card-white); }
  .card--back { top: 639px; background: var(--card-red); }

  .holder-name {
    position: absolute;
    left: 56px;
    top: 68px;
    margin: 0;
    font-size: 31px;
    font-weight: 400;
    color: var(--ink);
    line-height: 1;
  }
  .holder-role {
    position: absolute;
    left: 56px;
    top: 101px;
    margin: 0;
    font-size: 21px;
    font-weight: 400;
    color: var(--accent-red);
    line-height: 1;
  }
  .divider {
    position: absolute;
    left: 56px;
    top: 166px;
    width: 93px;
    height: 2px;
    background: var(--ink);
  }
  .address {
    position: absolute;
    left: 56px;
    top: 214px;
    margin: 0;
    font-style: normal;
    font-size: 20px;
    font-weight: 300;
    line-height: 25px;
    color: var(--ink-soft);
  }
  .contact-list {
    position: absolute;
    left: 56px;
    top: 312px;
    margin: 0;
    padding: 0;
    list-style: none;
    font-size: 20px;
    font-weight: 300;
    color: var(--ink-soft);
  }
  .contact-list li {
    display: flex;
    align-items: center;
    height: 26.5px;
  }
  .contact-list svg {
    width: 18px;
    height: 18px;
    margin-right: 12px;
    fill: var(--ink);
    flex: none;
  }

  .portrait {
    position: absolute;
    background: linear-gradient(180deg, #1a1a1a 0%, var(--silhouette) 100%);
    border-radius: 46% 46% 18% 18% / 30% 30% 12% 12%;
  }
  .portrait--front { left: 595px; top: 140px; width: 176px; height: 220px; }
  .portrait--back { left: 317px; top: 80px; width: 229px; height: 287px; }

  .brand-name {
    position: absolute;
    left: 573px;
    top: 364px;
    width: 220px;
    margin: 0;
    text-align: center;
    font-size: 34px;
    font-weight: 300;
    letter-spacing: 1px;
    color: var(--ink);
    line-height: 1;
  }

  .back-url {
    position: absolute;
    left: 0;
    right: 0;
    top: 410px;
    margin: 0;
    text-align: center;
    font-size: 19px;
    font-weight: 400;
    letter-spacing: 2.6px;
    color: var(--card-white);
  }
</style>
</head>
<body>
  <section class="card card--front">
    <h1 class="holder-name">Marc Ravoulet</h1>
    <p class="holder-role">Magician</p>
    <div class="divider"></div>
    <address class="address">MAGICIAN VERLINDO<br>17 rue des Tilleuls -<br>25990 VALMORINE</address>
    <ul class="contact-list">
      <li>
        <svg viewBox="0 0 24 24" aria-hidden="true"><path d="M6.6 10.8c1.4 2.8 3.8 5.1 6.6 6.6l2.2-2.2c.3-.3.7-.4 1-.2 1.1.4 2.3.6 3.6.6.6 0 1 .4 1 1V20c0 .6-.4 1-1 1C10.6 21 3 13.4 3 4c0-.6.4-1 1-1h3.5c.6 0 1 .4 1 1 0 1.3.2 2.5.6 3.6.1.3 0 .7-.2 1l-2.3 2.2z"/></svg>
        0381 946 157
      </li>
      <li>
        <svg viewBox="0 0 24 24" aria-hidden="true"><path d="M6.6 10.8c1.4 2.8 3.8 5.1 6.6 6.6l2.2-2.2c.3-.3.7-.4 1-.2 1.1.4 2.3.6 3.6.6.6 0 1 .4 1 1V20c0 .6-.4 1-1 1C10.6 21 3 13.4 3 4c0-.6.4-1 1-1h3.5c.6 0 1 .4 1 1 0 1.3.2 2.5.6 3.6.1.3 0 .7-.2 1l-2.3 2.2z"/></svg>
        0674 219 503
      </li>
      <li>
        <svg viewBox="0 0 24 24" aria-hidden="true"><path d="M2 5h20v14H2V5zm2 2v.3l8 5.6 8-5.6V7H4zm16 2.7-8 5.6-8-5.6V17h16V9.7z"/></svg>
        contact@verlindoillusions.example
      </li>
      <li>
        <svg viewBox="0 0 24 24" aria-hidden="true"><path d="M12 2a10 10 0 1 0 0 20 10 10 0 0 0 0-20zm-1 17.9A8 8 0 0 1 4.1 10l4.9 4.9v1c0 1.1.9 2 2 2v2zm6.9-2.5c-.3-.8-1-1.4-1.9-1.4h-1v-3c0-.6-.4-1-1-1H8v-2h2c.6 0 1-.4 1-1V7h2c1.1 0 2-.9 2-2v-.4a8 8 0 0 1 2.9 12.8z"/></svg>
        www.verlindoillusions.example
      </li>
    </ul>
    <div class="portrait portrait--front" role="img" aria-label="Black silhouette illustration of the magician in a jacket holding a playing card"></div>
    <p class="brand-name">VERLINDO</p>
  </section>

  <section class="card card--back">
    <div class="portrait portrait--back" role="img" aria-label="Black silhouette illustration of the magician in a jacket holding a playing card"></div>
    <p class="back-url">www.verlindoillusions.example</p>
  </section>
</body>
</html>
```